Stationary Set Rebrand for Brennick

We are a Canadian Distribution and Service Company that was established in 1969. Over the past 5 decades we have expanded our business and have warehouses across Canada. We specialize in adhesive tapes, adhesives, films, safety, warehouse, shipping, janitorial and packaging supplies.

We have updated our logo design and would like a new corporate branding identity that includes a new fresh Stationary Set (Business Cards, Letterhead, Letterhead MS Word, Envelope, Presentation Folders, Email Signatures, Notepad Covers, etc.)

Target Market(s)

Industrial Business Sector

Font styles to use
Sans Serif

Colors
0054AA
0677BA
7BADD7
CADEEF
E8F1F8
0094D4
00A9DD
6FCCEA
C7EBF8
E9F6FB
00AB8E
00BBA5
67D7C9
C6EFE9
E9F9F6
EB3D1F
EC4F4E
F09395
F8D3D4
FCEDEE

Requirements
Should not have
• Colors not too light, darker colours preferred

```html
<!DOCTYPE html>
<html lang="en">
<head>
<meta charset="utf-8">
<title>Brennick Stationery Set</title>
<link rel="stylesheet" href="https://fonts.googleapis.com/css2?family=Poppins:wght@400;500;600;700&family=Open+Sans:wght@400;600&display=swap">
<style>
:root{
  --ink:#1d1c24;
  --red:#dc1024;
  --white:#ffffff;
  --paper:#f7f7f7;
  --stage:#d5dadd;
  --muted:#5c5c66;
  --rule:#c9ced2;
}
*{box-sizing:border-box;margin:0;padding:0}
html,body{width:1200px;height:711px;overflow:hidden}
body{background:var(--stage);font-family:"Poppins",sans-serif;position:relative;color:var(--ink)}
.piece{position:absolute;overflow:hidden;box-shadow:0 6px 14px rgba(0,0,0,.28)}
.wordmark{font-family:"Poppins",sans-serif;font-weight:700;letter-spacing:-.5px;line-height:1;display:flex;align-items:center;gap:4px}
.wordmark .dot{width:.28em;height:.28em;background:var(--red);display:inline-block}
.band{position:absolute;left:0;right:0;bottom:0;background:var(--red)}
.contact{position:absolute;right:12px;text-align:right;color:var(--white);font-size:6.2px;line-height:1.3}
.contact li{list-style:none;display:flex;justify-content:flex-end;align-items:center;gap:5px}
.ico{width:6px;height:6px;fill:var(--white)}

/* envelope */
.envelope-front{left:51px;top:55px;width:282px;height:126px;background:var(--ink)}
.envelope-front .wordmark{position:absolute;left:20px;top:12px;font-size:20px;color:var(--white)}
.envelope-front .band{height:49px}
.envelope-front .contact{top:8px}
.envelope-back{left:52px;top:193px;width:281px;height:125px;background:var(--ink)}
.envelope-back .flap{position:absolute;left:0;top:0;width:100%;height:43px;background:var(--red);border-radius:0 0 10px 10px;margin:0}
.envelope-back .flap-mark{position:absolute;left:50%;top:17px;width:9px;height:9px;background:var(--ink);transform:translateX(-50%)}

/* business cards */
.card-back{left:53px;top:329px;width:274px;height:156px;background:var(--ink)}
.card-back .texture{position:absolute;inset:0;background:linear-gradient(200deg,#6a6a72 0%,#2b2a33 35%,#1a1920 100%)}
.card-back .wordmark{position:absolute;left:54px;top:55px;font-size:40px;color:var(--white)}
.card-front{left:53px;top:501px;width:274px;height:156px;background:var(--red)}
.card-front .corner{position:absolute;left:0;top:0;width:90px;height:60px;background:var(--ink);clip-path:polygon(0 0,100% 0,0 100%)}
.card-front .wordmark{position:absolute;right:10px;top:10px;font-size:30px;color:var(--white)}
.card-front .person{position:absolute;right:12px;top:66px;text-align:right;color:var(--white)}
.card-front .person .name{font-size:13px;font-weight:400;line-height:1.1}
.card-front .person .name b{font-weight:600}
.card-front .person .role{font-size:6.5px}
.card-front .tick{position:absolute;right:0;top:69px;width:7px;height:18px;background:var(--white)}
.card-front .addr{position:absolute;right:12px;top:96px;text-align:right;color:var(--white);font-size:7px;line-height:1.3}
.card-front .contact{top:120px;font-size:7px;right:12px}
.card-front .contact .ico{width:6.5px;height:6.5px}

/* letterhead */
.letterhead{left:367px;top:57px;width:330px;height:466px;background:var(--white)}
.letterhead .wordmark{position:absolute;left:0;right:0;top:16px;justify-content:center;font-size:24px;color:var(--ink)}
.letterhead .rule{position:absolute;left:17px;right:17px;top:52px;height:1px;background:#555}
.letterhead .rule span{position:absolute;left:95px;width:107px;top:-1px;height:2px;background:var(--red)}
.letter{position:absolute;left:18px;right:18px;top:112px;font-family:"Open Sans",sans-serif;font-size:6.4px;line-height:1.4;color:#222}
.letter .date{margin-bottom:8px}
.letter .to{font-family:"Poppins",sans-serif;font-weight:600;font-size:8.5px;line-height:1.1}
.letter .addr{margin:6px 0 14px}
.letter .salutation{font-family:"Poppins",sans-serif;font-weight:600;font-size:8.5px;margin-bottom:7px}
.letter p{text-align:justify;margin-bottom:8px}
.letter .sign{margin-top:22px;height:22px;width:90px;border-bottom:1px solid #333;opacity:.6}
.letter .signer{font-family:"Poppins",sans-serif;font-weight:600;font-size:14px;line-height:1.2;margin-top:2px}
.letterhead .band{height:57px}
.letterhead .contact{top:7px;font-size:7.2px;right:20px}
.letterhead .contact .ico{width:6.5px;height:6.5px}

/* email signature */
.email-signature{left:365px;top:546px;width:331px;height:110px;background:var(--ink)}
.email-signature .wordmark{position:absolute;left:15px;top:8px;font-size:27px;color:var(--white)}
.email-signature .person{position:absolute;right:16px;top:7px;text-align:right}
.email-signature .person .name{color:var(--red);font-size:14px;line-height:1.1}
.email-signature .person .name b{font-weight:600}
.email-signature .person .role{color:var(--white);font-size:6.5px}
.email-signature .band{height:48px}
.email-signature .contact{top:5px;font-size:7px;right:20px}
.social{position:absolute;left:54px;bottom:7px;display:flex;gap:3px}
.social i{display:block;width:5px;height:5px;border-radius:50%;background:var(--white)}

/* folder */
.folder-cover{left:727px;top:46px;width:122px;height:236px;background:var(--ink)}
.folder-cover .glow{position:absolute;left:0;right:0;top:40px;height:130px;background:radial-gradient(ellipse at 50% 40%,#9d1520 0%,#3a1a20 55%,transparent 75%)}
.folder-cover .wordmark{position:absolute;right:10px;bottom:16px;font-size:16px;color:var(--white)}
.folder-inside{left:912px;top:60px;width:228px;height:211px;background:linear-gradient(90deg,#f4f4f4 0%,#e6e6e6 50%,#d4d4d4 50%,#c9c9c9 100%)}
.pocket{position:absolute;bottom:0;width:114px;height:70px;background:var(--red)}
.pocket.left{left:0;border-top-right-radius:40px 30px}
.pocket.right{right:0;border-top-left-radius:40px 30px;background:#c80f20}
.pocket .mark{position:absolute;left:50%;top:24px;width:12px;height:12px;background:var(--white);transform:translateX(-50%)}

/* notebook */
.notebook-cover{left:830px;top:298px;width:240px;height:140px;background:var(--ink)}
.notebook-cover .texture{position:absolute;inset:0;background:linear-gradient(160deg,#4a4a52 0%,#26252d 40%,#17161c 100%)}
.notebook-cover .spiral{position:absolute;left:0;top:0;bottom:0;width:8px;background:repeating-linear-gradient(180deg,#bfc3c6 0 2px,transparent 2px 4px)}
.notebook-cover .wordmark{position:absolute;right:14px;bottom:14px;font-size:17px;color:var(--white)}
.notebook-open{left:782px;top:462px;width:274px;height:193px;background:var(--white);display:flex}
.page{position:relative;flex:1;padding:12px 8px 0 10px}
.page + .page{border-left:8px solid #b7bcc0}
.page .head{display:flex;justify-content:space-between;align-items:flex-start;border-bottom:1px solid var(--red);padding-bottom:2px}
.page .label{font-size:4.5px;color:var(--red);line-height:1.3}
.page .label small{display:block;color:#777;font-size:3.6px}
.page .wordmark{font-size:10px;color:var(--ink)}
.page .lines{position:absolute;left:10px;right:8px;top:38px;bottom:10px;background:repeating-linear-gradient(180deg,transparent 0 9px,var(--rule) 9px 10px)}
.page .fade{position:absolute;left:30px;top:60px;width:60px;height:90px;background:radial-gradient(ellipse,#f6e4dd 0%,transparent 70%)}
</style>
</head>
<body>
<svg width="0" height="0" style="position:absolute" aria-hidden="true">
  <defs>
    <symbol id="i-phone" viewBox="0 0 10 10"><path d="M2 1l2 0 1 2.5-1.2 1a6 6 0 0 0 2.7 2.7l1-1.2L10 7v2a1 1 0 0 1-1 1A9 9 0 0 1 0 1a1 1 0 0 1 1-1z"/></symbol>
    <symbol id="i-mail" viewBox="0 0 10 10"><path d="M0 2h10v6H0z M0 2l5 3.5L10 2" fill="none" stroke="#fff" stroke-width="1.2"/></symbol>
    <symbol id="i-web" viewBox="0 0 10 10"><circle cx="5" cy="5" r="4.2" fill="none" stroke="#fff" stroke-width="1.2"/><path d="M1 5h8M5 1v8" stroke="#fff" stroke-width="1"/></symbol>
    <symbol id="i-pin" viewBox="0 0 10 10"><path d="M5 0a3.6 3.6 0 0 1 3.6 3.6C8.6 6.5 5 10 5 10S1.4 6.5 1.4 3.6A3.6 3.6 0 0 1 5 0zm0 2.2a1.4 1.4 0 1 0 0 2.8 1.4 1.4 0 0 0 0-2.8z"/></symbol>
  </defs>
</svg>

<section class="piece envelope-front">
  <div class="wordmark">Brennick<span class="dot"></span></div>
  <div class="band">
    <ul class="contact">
      <li>(555) 014-2290 <svg class="ico"><use href="#i-phone"/></svg></li>
      <li>hello@brennicksupply.ca <svg class="ico"><use href="#i-mail"/></svg></li>
      <li>www.brennicksupply.ca <svg class="ico"><use href="#i-web"/></svg></li>
      <li style="margin-top:2px">88 Harbour Rd. Unit 4 Hamilton, ON L8L 1A1 <svg class="ico"><use href="#i-pin"/></svg></li>
    </ul>
  </div>
</section>

<section class="piece envelope-back">
  <div class="flap"></div>
  <span class="flap-mark"></span>
</section>

<section class="piece card-back">
  <div class="texture" role="img" aria-label="Embossed repeating brand-mark pattern on dark card stock"></div>
  <div class="wordmark">Brennick</div>
</section>

<section class="piece card-front">
  <div class="corner"></div>
  <div class="wordmark">Brennick</div>
  <div class="person">
    <div class="name"><b>Petra</b> Lindqvist</div>
    <div class="role">Founder &amp; CEO</div>
  </div>
  <span class="tick"></span>
  <div class="addr">88 Harbour Rd. Unit 4<br>Hamilton, ON L8L 1A1</div>
  <ul class="contact">
    <li>(555) 014-2290 <svg class="ico"><use href="#i-phone"/></svg></li>
    <li>hello@brennicksupply.ca <svg class="ico"><use href="#i-mail"/></svg></li>
    <li>www.brennicksupply.ca <svg class="ico"><use href="#i-web"/></svg></li>
  </ul>
</section>

<section class="piece letterhead">
  <div class="wordmark">Brennick<span class="dot"></span></div>
  <div class="rule"><span></span></div>
  <div class="letter">
    <div class="date">August-05-2019</div>
    <div class="to">Dana Whitlow</div>
    <div>Director</div>
    <div class="addr">88 Harbour Rd. Unit 4<br>Hamilton, ON L8L 1A1</div>
    <div class="salutation">Dana Whitlow</div>
    <p>Lorem ipsum dolor sit amet, consectetuer adipiscing elit, sed diam nonummy nibh euismod tincidunt ut laoreet dolore magna aliquam erat volutpat. Ut wisi enim ad minim veniam, quis nostrud exerci tation ullamcorper suscipit lobortis</p>
    <p>Lorem ipsum dolor sit amet, cons ectetuer adipiscing elit, sed diam nonummy nibh euismod tincidunt ut laoreet dolore magna aliquam erat volutpat. Ut wisi enim ad minim veniam, quis nostrud exerci tation ullamcorper suscipit lobortis nisl ut aliquip ex ea commodo consequat. Lorem ipsum dolor sit amet, consectetuer olutpat. Ut wisi enim ad minim veniam, quis nostrud exerci tation ullamcorper suscipit lobortis nisl ut aliquip ex ea commodo consequat. Duis autem</p>
    <p>vel eum iriure dolor in hendrerit in vulputate velit esse molestie consequat, vel illum dolore eu feugiat nulla facilisis at vero eros et accumsan et iusto odio dignissim qui blandit praesent luptatum zzril delenit augue duis dolore te feugait nulla facilisi. Lorem ipsum dolor sit amet, cons ectetuer adipiscing elit, sed diam nonummy nibh euismod tincidunt ut laoreet dolore magna aliquam erat volutpat. Ut wisi enim .</p>
    <div class="sign" role="img" aria-label="Handwritten signature"></div>
    <div class="signer">Owen Hale</div>
    <div>Co-Founder</div>
  </div>
  <div class="band">
    <ul class="contact">
      <li>(555) 014-2290 <svg class="ico"><use href="#i-phone"/></svg></li>
      <li>hello@brennicksupply.ca <svg class="ico"><use href="#i-mail"/></svg></li>
      <li>www.brennicksupply.ca <svg class="ico"><use href="#i-web"/></svg></li>
      <li style="margin-top:2px">88 Harbour Rd. Unit 4 Hamilton, ON L8L 1A1 <svg class="ico"><use href="#i-pin"/></svg></li>
    </ul>
  </div>
</section>

<section class="piece email-signature">
  <div class="wordmark">Brennick<span class="dot"></span></div>
  <div class="person">
    <div class="name"><b>Petra</b> Lindqvist</div>
    <div class="role">Founder &amp; CEO</div>
  </div>
  <div class="band">
    <div class="social"><i></i><i></i><i></i><i></i><i></i></div>
    <ul class="contact">
      <li>(555) 014-2290 <svg class="ico"><use href="#i-phone"/></svg></li>
      <li>hello@brennicksupply.ca <svg class="ico"><use href="#i-mail"/></svg></li>
      <li>www.brennicksupply.ca <svg class="ico"><use href="#i-web"/></svg></li>
      <li style="margin-top:2px">88 Harbour Rd. Unit 4 Hamilton, ON L8L 1A1 <svg class="ico"><use href="#i-pin"/></svg></li>
    </ul>
  </div>
</section>

<section class="piece folder-cover">
  <div class="glow"></div>
  <div class="wordmark">Brennick</div>
</section>

<section class="piece folder-inside">
  <div class="pocket left"><span class="mark"></span></div>
  <div class="pocket right"><span class="mark"></span></div>
</section>

<section class="piece notebook-cover">
  <div class="texture" role="img" aria-label="Repeating embossed brand-mark pattern on notebook cover"></div>
  <div class="spiral"></div>
  <div class="wordmark">Brennick</div>
</section>

<section class="piece notebook-open">
  <div class="page">
    <div class="head"><div class="label">Notes<small>Date Of</small></div><div class="wordmark">Brennick</div></div>
    <div class="fade"></div>
    <div class="lines"></div>
  </div>
  <div class="page">
    <div class="head"><div class="label">Notes<small>Date Of</small></div><div class="wordmark">Brennick</div></div>
    <div class="fade"></div>
    <div class="lines"></div>
  </div>
</section>
</body>
</html>
```